Catalogue Design Project

We need a catalog design for a new private university called Redwell Institute Bayshore (see website www.rwi-bs.org). The catalog should be about 30 pages maximum and will include items such as General Information, Academic schedule, department descriptions, program descriptions, course descriptions, school policies, student services, admissions, San diego Lifestyle, etc.
I will provide the text but I need a professional design with regard to page layouts. I have provided some examples.
Ok, i posted the catalog content, just missing course descriptions.
Target Market(s)
Young Professionals, Foreign Students
Industry/Entity Type
University
Look and feel
Each slider illustrates characteristics of the customer's brand and the style your logo design should communicate.

```html
<!DOCTYPE html>
<html lang="en">
<head>
<meta charset="utf-8">
<title>Academic Calendar – Redwell Institute Bayshore</title>
<link href="https://fonts.googleapis.com/css2?family=Carlito:wght@400;700&display=swap" rel="stylesheet">
<style>
  :root {
    --paper: #ffffff;
    --ink: #1c1c1c;
    --row-fill: #e3e3e4;
    --rule: #3a3a3a;
    --brand-blue: #1f5a96;
    --brand-blue-deep: #15477d;
    --accent-line: #5b86b8;
    --footer-line: #9cb3cf;
    --footer-ink: #7a7a7a;
  }
  * { margin: 0; padding: 0; box-sizing: border-box; }
  html, body { width: 927px; height: 1200px; overflow: hidden; background: var(--paper); }
  body { font-family: "Carlito", "Calibri", sans-serif; color: var(--ink); }

  .page { position: relative; width: 927px; height: 1200px; overflow: hidden; }

  .brand-name {
    position: absolute; left: 58px; top: 40px;
    display: flex; align-items: center; gap: 10px;
    font-size: 20px; font-weight: 400; color: var(--brand-blue); letter-spacing: 0.3px;
  }
  .brand-name .brand-mark {
    width: 14px; height: 14px; border-radius: 50%; background: var(--brand-blue);
  }

  .header-photo {
    position: absolute; right: 0; top: 0; width: 390px; height: 146px;
    background: linear-gradient(100deg, rgba(255,255,255,1) 0%, rgba(236,240,244,0.6) 30%, #dfe4ea 70%, #cfd6de 100%);
  }

  .header-rule {
    position: absolute; left: 0; top: 102px; width: 927px; height: 2px;
    background: var(--accent-line);
  }
  .header-banner {
    position: absolute; left: 553px; top: 103px; width: 374px; height: 46px;
    background: linear-gradient(180deg, var(--brand-blue) 0%, var(--brand-blue-deep) 100%);
    clip-path: polygon(0 0, 100% 0, 100% 100%, 28px 100%);
    color: #fff; font-size: 30px; letter-spacing: 0.3px;
    display: flex; align-items: center; justify-content: flex-end; padding-right: 22px;
  }

  .term { position: absolute; left: 79px; width: 803px; }
  .term-title {
    display: flex; justify-content: space-between;
    font-size: 18px; font-weight: 400; line-height: 22px; margin-bottom: 10px;
  }
  .schedule { width: 100%; border-collapse: collapse; font-size: 18px; }
  .schedule td {
    height: 34.5px; background: var(--row-fill);
    border: 1.5px solid var(--rule); padding: 3px 0 0; vertical-align: middle;
  }
  .schedule .date { width: 310px; padding-left: 30px; }
  .schedule .event { padding-left: 33px; }

  .term-fall   { top: 205px; }
  .term-winter { top: 486px; }
  .term-spring { top: 661px; }
  .term-summer { top: 940px; }

  .footer-rule {
    position: absolute; left: 0; top: 1158px; width: 927px; height: 1px; background: var(--footer-line);
  }
  .footer-mark {
    position: absolute; right: 41px; top: 1172px; font-size: 12px; color: var(--footer-ink); letter-spacing: 0.3px;
  }
</style>
</head>
<body>
<div class="page">

  <div class="brand-name"><span class="brand-mark"></span><span>Redwell Institute Bayshore</span></div>

  <div class="header-photo" role="img" aria-label="Close-up of a paper calendar page with day numbers, fading into white"></div>
  <div class="header-rule"></div>
  <div class="header-banner">ACADEMIC CALENDAR</div>

  <section class="term term-fall">
    <h2 class="term-title"><span>2012 Fall Quarter:&nbsp; September 4th, 2012 – December 23, 2012</span><span>Enrollment Deadline: 8/17/12</span></h2>
    <table class="schedule">
      <tr><td class="date">Tuesday, September 4</td><td class="event">Session A Begins</td></tr>
      <tr><td class="date">Sunday, September 9</td><td class="event">Deadline to Add/Drop Session A</td></tr>
      <tr><td class="date">Sunday, October 28</td><td class="event">Session A Ends</td></tr>
      <tr><td class="date">Monday, October 29</td><td class="event">Session B Begins</td></tr>
      <tr><td class="date">Sunday, November 4</td><td class="event">Deadline to Add/Drop Session B</td></tr>
      <tr><td class="date">Sunday, December 23</td><td class="event">Session B Ends</td></tr>
    </table>
  </section>

  <section class="term term-winter">
    <h2 class="term-title"><span>2013 Winter Quarter:&nbsp; January 7, 2013 – March 3, 2013</span><span>Enrollment Deadline: 12/23/12</span></h2>
    <table class="schedule">
      <tr><td class="date">Monday, January 7</td><td class="event">Session A Begins</td></tr>
      <tr><td class="date">Sunday, January 13</td><td class="event">Deadline to Add/Drop Session A</td></tr>
      <tr><td class="date">March 3, 2013</td><td class="event">Session A Ends</td></tr>
    </table>
  </section>

  <section class="term term-spring">
    <h2 class="term-title"><span>2013 Spring Semester:&nbsp; March 11, 2013 – June 30, 2013</span><span>Enrollment Deadline: 2/24/13</span></h2>
    <table class="schedule">
      <tr><td class="date">Monday, March 11</td><td class="event">Session A Begins</td></tr>
      <tr><td class="date">Sunday, March 17</td><td class="event">Deadline to Add/Drop Session A</td></tr>
      <tr><td class="date">Sunday, May 5</td><td class="event">Session A Ends</td></tr>
      <tr><td class="date">Monday, May 6</td><td class="event">Session B Begins</td></tr>
      <tr><td class="date">Sunday, May 12</td><td class="event">Deadline to Add/Drop Session B</td></tr>
      <tr><td class="date">Sunday, June 30</td><td class="event">Session B Ends</td></tr>
    </table>
  </section>

  <section class="term term-summer">
    <h2 class="term-title"><span>2013 Summer Semester:&nbsp; July 8, 2013 – September 1, 2013</span><span>Enrollment Deadline: 6/16/13</span></h2>
    <table class="schedule">
      <tr><td class="date">Monday, July 8</td><td class="event">Session A Begins</td></tr>
      <tr><td class="date">Sunday, July 14</td><td class="event">Deadline to Add/Drop Session A</td></tr>
      <tr><td class="date">Sunday, September 1</td><td class="event">Session A Ends</td></tr>
    </table>
  </section>

  <div class="footer-rule"></div>
  <div class="footer-mark">5::: REDWELL INSTITUTE</div>

</div>
</body>
</html>
```